Boutique Technology Consultancy specialising is Electronic and physical security

We need to redo our existing outdated website. For your reference the link www.pelu.com.au

```html
<!DOCTYPE html>
<html lang="en">
<head>
<meta charset="utf-8">
<title>Pelu Services</title>
<link rel="stylesheet" href="https://fonts.googleapis.com/css2?family=Montserrat:wght@500;600;700&family=Lato:wght@400;700&display=swap">
<style>
:root{
  --red:#d0282a;
  --red-dark:#8e1418;
  --black:#000;
  --ink:#0a0a0c;
  --navy:#120f22;
  --white:#fff;
  --muted:#d9d9d9;
  --line:#e6e6e6;
}
*{box-sizing:border-box;margin:0;padding:0}
html,body{width:1200px;height:3939px;overflow:hidden;background:var(--black)}
body{position:relative;font-family:"Lato",sans-serif;color:var(--white)}
.abs{position:absolute}
.heading-font{font-family:"Montserrat",sans-serif}
.btn{position:absolute;display:flex;align-items:center;justify-content:center;border-radius:24px;
  background:linear-gradient(90deg,var(--red-dark),var(--red));color:var(--white);
  font-family:"Montserrat",sans-serif;font-weight:600;font-size:16px;text-transform:uppercase}
.brand{font-family:"Montserrat",sans-serif;font-weight:700;color:var(--white);display:flex;align-items:center;gap:12px}
.brand .mark{width:18px;height:18px;background:var(--red)}

/* nav */
.site-nav{top:0;left:0;width:1200px;height:85px;z-index:3}
.site-nav .brand{position:absolute;left:100px;top:24px;font-size:30px}
.nav-links{position:absolute;left:472px;top:33px;display:flex;gap:31px;font-family:"Montserrat",sans-serif;font-size:15px;font-weight:500}
.site-nav .btn{left:969px;top:20px;width:132px;height:46px;font-size:15px}

/* hero */
.hero{top:0;left:0;width:1200px;height:685px;
  background:radial-gradient(ellipse at 80% 40%,#3a1518 0%,#1c1c1f 40%,#0c0c0e 100%)}
.hero-art{left:640px;top:130px;width:460px;height:500px;
  background:radial-gradient(circle at 50% 50%,rgba(208,40,42,.55),rgba(208,40,42,0) 65%)}
.hero h1{position:absolute;left:100px;top:222px;font-family:"Montserrat",sans-serif;font-weight:700;font-size:46px;line-height:64px;letter-spacing:1px;text-transform:uppercase}
.hero p{position:absolute;left:97px;top:356px;width:400px;font-size:15px;line-height:31px}
.hero .btn{left:100px;top:470px;width:143px;height:46px}

/* section headings */
.sec-title{position:absolute;left:0;width:1200px;text-align:center;font-family:"Montserrat",sans-serif;font-weight:700;font-size:31px;text-transform:uppercase;display:flex;justify-content:center;align-items:center;gap:10px}
.sec-title::before,.sec-title::after{content:"";width:44px;height:3px;background:var(--red);margin-top:16px}
.sec-lead{position:absolute;left:170px;width:860px;text-align:center;font-size:15px;line-height:31px}

/* services */
.services{top:685px;left:0;width:1200px;height:762px;background:var(--black)}
.svc-col{position:absolute;top:0}
.svc-icon{width:50px;height:54px;border:2px solid var(--red);border-radius:8px;opacity:.85}
.svc-col h3{font-family:"Montserrat",sans-serif;font-weight:600;font-size:18px;margin-top:14px}
.svc-col ul{list-style:none;margin-top:14px}
.svc-col li{position:relative;padding-left:21px;font-size:15px;line-height:34px}
.svc-col li::before{content:"";position:absolute;left:1px;top:14px;width:8px;height:8px;border-radius:50%;background:var(--white)}
.svc-divider{position:absolute;top:313px;width:2px;height:255px;background:var(--line)}
.services .btn{left:529px;top:640px;width:143px;height:46px}

/* about */
.about{top:1447px;left:0;width:1200px;height:646px;
  background:radial-gradient(ellipse at 10% 80%,#2a1e55 0%,transparent 45%),radial-gradient(ellipse at 60% 0%,#1e1a40 0%,transparent 50%),var(--navy)}
.about-photo{left:98px;top:101px;width:455px;height:459px;border-radius:12px;
  background:linear-gradient(135deg,#6b6b6b,#2b2b2b 60%,#9a9a9a)}
.about h2{position:absolute;left:698px;top:94px;font-family:"Montserrat",sans-serif;font-weight:700;font-size:27px;display:flex;align-items:center;gap:12px}
.about h2::after{content:"";width:46px;height:3px;background:var(--red);margin-top:12px}
.about-text{position:absolute;left:652px;top:148px;width:460px;font-size:15px;line-height:31px}
.about-text p+p{margin-top:10px}
.about .btn{left:652px;top:505px;width:143px;height:46px}

/* experience */
.experience{top:2093px;left:0;width:1200px;height:772px;background:var(--black)}
.card{position:absolute;top:287px;width:317px;height:405px}
.card-photo{width:317px;height:205px;border-radius:12px 12px 0 0;background:linear-gradient(160deg,#d8d8d8,#5a5a5a 55%,#1d1d1d)}
.card-body{height:200px;border:4px solid var(--red);border-top:none;border-radius:0 0 14px 14px;text-align:center;padding-top:30px}
.card h3{font-family:"Montserrat",sans-serif;font-weight:700;font-size:18px}
.card p{font-size:15px;line-height:31px;margin-top:10px;padding:0 12px}

/* contact */
.contact{top:2865px;left:0;width:1200px;height:535px;
  background:linear-gradient(180deg,#0a0a0c,#1b1b1f 50%,#101013)}
.field{position:absolute;border:1.5px solid var(--muted);border-radius:8px;font-size:14px;padding:15px 17px}
.contact .btn{left:531px;top:417px;width:136px;height:44px;text-transform:none}

/* footer */
.footer{top:3400px;left:0;width:1200px;height:539px;
  background:radial-gradient(ellipse at 50% 30%,#1b1b1e,#070708 70%)}
.footer .brand{position:absolute;left:0;width:1200px;justify-content:center;top:118px;font-size:46px}
.foot-links{position:absolute;left:0;width:1200px;top:228px;display:flex;justify-content:center;gap:31px;font-family:"Montserrat",sans-serif;font-size:15px;font-weight:500}
.foot-item{position:absolute;top:300px;display:flex;gap:22px}
.foot-icon{width:44px;height:44px;border-radius:50%;background:var(--red-dark);display:flex;align-items:center;justify-content:center;margin-top:4px}
.foot-item b{display:block;font-family:"Montserrat",sans-serif;font-weight:600;font-size:15px;line-height:31px}
.foot-item span{display:block;font-size:15px;line-height:31px}
.copyright{position:absolute;left:0;width:1200px;top:404px;text-align:center;font-size:15px}
.copyright em{font-style:normal;color:var(--red)}
.socials{position:absolute;left:524px;top:458px;display:flex;gap:13px}
.socials i{display:block;width:28px;height:28px;border-radius:50%;background:var(--red)}
</style>
</head>
<body>

<section class="hero abs">
  <div class="hero-art abs" role="img" aria-label="Abstract red geometric shape over a dark network backdrop"></div>
  <h1>Welcome to<br>Pelu Services</h1>
  <p>Pelu Services was established in 2016 by Rob Halden to provide technology consulting services to corporate and government clients</p>
  <a class="btn">Get Started</a>
</section>

<header class="site-nav abs">
  <div class="brand"><span class="mark"></span>Pelu Services</div>
  <nav class="nav-links"><span>WELCOME</span><span>EXPERIENCE</span><span>SERVICES</span><span>TEAM</span><span>ABOUT</span></nav>
  <a class="btn">Contact</a>
</header>

<section class="services abs">
  <h2 class="sec-title" style="top:128px">Our Services</h2>
  <p class="sec-lead" style="top:190px">Pelu Services provides independent professional services for projects as well as operations and maintenance. We offer end to end services including:</p>

  <div class="svc-col" style="left:138px;top:278px">
    <div class="svc-icon" role="img" aria-label="Strategy icon"></div>
    <h3>Strategy</h3>
    <ul><li>Technology roadmaps;</li><li>Master standards; and</li><li>Asset management plans.</li></ul>
  </div>
  <div class="svc-divider" style="left:413px"></div>
  <div class="svc-col" style="left:503px;top:278px">
    <div class="svc-icon" role="img" aria-label="Projects icon"></div>
    <h3>Projects</h3>
    <ul><li>Audit;</li><li>Design;</li><li>Procurement;</li><li>Technical project</li><li>management; and</li><li>Witness testing.</li></ul>
  </div>
  <div class="svc-divider" style="left:731px"></div>
  <div class="svc-col" style="left:795px;top:278px">
    <div class="svc-icon" role="img" aria-label="Operations icon"></div>
    <h3>Operations and maintenance</h3>
    <ul><li>ervice and maintenance<br>specifications;</li><li>Policies and procedures;</li><li>Procurement; and</li><li>Service reviews.</li></ul>
  </div>
  <a class="btn">View More</a>
</section>

<section class="about abs">
  <div class="about-photo abs" role="img" aria-label="Black and white photo of a team meeting around a boardroom table"></div>
  <h2>ABOUT US</h2>
  <div class="about-text">
    <p>Pelu Services was established in 2016 by Rob Halden to provide technology consulting services to corporate and government clients with a focus on:</p>
    <p>Property/facilities management<br>Asset management<br>Development and Construction</p>
    <p>In 2022, Pelu Services merged Norvik Group into its operations, bringing increased capacity and capability to the NSW office.Pelu is a privately owned independent consultancy 100% dedicated to customer satisfaction.</p>
  </div>
  <a class="btn">Read More</a>
</section>

<section class="experience abs">
  <h2 class="sec-title" style="top:132px">Our Experience</h2>
  <p class="sec-lead" style="top:188px;left:150px;width:900px">Pelu has a diverse range of project experience across a range of industries within both the public and private sectors. The following is a small sample of some of the clients and sites we have worked with.</p>

  <article class="card" style="left:98px">
    <div class="card-photo" role="img" aria-label="Glass dome roof over a historic tower"></div>
    <div class="card-body"><h3>Harbour Central</h3><p>Security technology design consulting for this popular retail and entertainment hub which is managed by the Kestrel Group.</p></div>
  </article>
  <article class="card" style="left:441px">
    <div class="card-photo" role="img" aria-label="Motorway with an overhead gantry"></div>
    <div class="card-body"><h3>Southway</h3><p>Virtual servers, network and CCTV upgrade design and project management for Public Private Partnership (PPP).</p></div>
  </article>
  <article class="card" style="left:783px">
    <div class="card-photo" role="img" aria-label="Modern hospital building entrance"></div>
    <div class="card-body"><h3>Northgate Women's Hospital</h3><p>Security technology design consulting for this popular retail and entertainment hub which is managed by the Kestrel Group.</p></div>
  </article>
</section>

<section class="contact abs">
  <h2 class="sec-title" style="top:108px">Contact Us</h2>
  <div class="field" style="left:181px;top:183px;width:413px;height:51px">Name</div>
  <div class="field" style="left:605px;top:183px;width:413px;height:51px">Email</div>
  <div class="field" style="left:181px;top:245px;width:413px;height:51px">Phone Number</div>
  <div class="field" style="left:605px;top:245px;width:413px;height:51px">Subject</div>
  <div class="field" style="left:181px;top:307px;width:837px;height:89px">Message</div>
  <a class="btn">Submit</a>
</section>

<footer class="footer abs">
  <div class="brand"><span class="mark" style="width:26px;height:26px"></span>Pelu Services</div>
  <nav class="foot-links"><span>WELCOME</span><span>EXPERIENCE</span><span>SERVICES</span><span>TEAM</span><span>ABOUT</span><span>CONTACT US</span></nav>

  <div class="foot-item" style="left:125px">
    <div class="foot-icon"><svg width="16" height="16" viewBox="0 0 24 24"><path fill="#fff" d="M6.6 10.8a15 15 0 006.6 6.6l2.2-2.2a1 1 0 011-.25 11.4 11.4 0 003.6.6 1 1 0 011 1V20a1 1 0 01-1 1A17 17 0 013 4a1 1 0 011-1h3.5a1 1 0 011 1c0 1.25.2 2.45.6 3.6a1 1 0 01-.25 1z"/></svg></div>
    <div><b>PHONE:</b><span>1300 555 018</span></div>
  </div>
  <div class="foot-item" style="left:433px">
    <div class="foot-icon"><svg width="16" height="16" viewBox="0 0 24 24"><path fill="#fff" d="M3 6h18v12H3z"/><path fill="none" stroke="#8e1418" stroke-width="2" d="M3 6l9 7 9-7"/></svg></div>
    <div><b>EMAIL:</b><span>hello@pelu.com.au</span></div>
  </div>
  <div class="foot-item" style="left:828px">
    <div class="foot-icon"><svg width="14" height="18" viewBox="0 0 24 30"><path fill="#fff" d="M12 0a10 10 0 00-10 10c0 8 10 20 10 20s10-12 10-20A10 10 0 0012 0zm0 14a4 4 0 110-8 4 4 0 010 8z"/></svg></div>
    <div><b>ADDRESS:</b><span>GPO Box 1042</span><span>MELBOURNE VIC 3001</span></div>
  </div>

  <p class="copyright">Copyrights@2023.<em>Pelu Services</em>.All Rights Reserved</p>
  <div class="socials" aria-label="Social links"><i></i><i></i><i></i><i></i></div>
</footer>

</body>
</html>
```